Business cards and stationary design

We just completed the design of our new logo and we need to print new business cards and letterhead for our nonprofit. We are looking for a fresh new design that shows off our new logo. On letterhead, we must have a column on the right or left to include our Board of Directors (up to 45 names) (see attachment)

Industry/Entity Type

Non-Profit

Contact Information for Business Card

Standard business card with name, title, Company name, mailing address phone numbers, email address and website. Tagline on back "Bringing the homeless home"

Font styles to use
Sans Serif

Requirements
Must have
• include pertinent information above
• new logo
• fonts compatible with logo
• should use logo colors only
Nice to have
• tag lines

```html
<!DOCTYPE html>
<html lang="en">
<head>
<meta charset="utf-8">
<title>Harborlight Homes – Business Card</title>
<link href="https://fonts.googleapis.com/css2?family=Michroma&family=Arimo:wght@400&display=swap" rel="stylesheet">
<style>
  :root {
    --bg: #d9d9d9;
    --card: #f8f8f8;
    --teal: #1a86a6;
    --red: #e2252b;
    --text: #555555;
    --tint-blue: #dfedf2;
    --tint-cream: #faf1df;
  }
  * { margin: 0; padding: 0; box-sizing: border-box; }
  html, body { width: 1200px; height: 582px; overflow: hidden; }
  body { background: var(--bg); position: relative; font-family: "Arimo", Arial, sans-serif; }

  .card {
    position: absolute;
    top: 159px;
    width: 464px;
    height: 264px;
    background: var(--card);
    box-shadow: 1px 2px 4px rgba(0,0,0,0.35);
    overflow: hidden;
  }
  .card--front { left: 128px; }
  .card--back { left: 608px; }

  .decor {
    position: absolute;
    top: 0;
    height: 100%;
    width: 166px;
    background: linear-gradient(180deg, var(--tint-cream) 0%, var(--tint-blue) 100%);
    opacity: 0.7;
  }
  .card--front .decor { right: 0; }
  .card--back .decor { left: 0; }

  .contact { position: absolute; left: 50px; top: 70px; }
  .contact__name {
    font-family: "Michroma", Arial, sans-serif;
    font-size: 14px;
    letter-spacing: 1px;
    color: var(--teal);
    line-height: 1.2;
  }
  .contact__title {
    font-family: "Michroma", Arial, sans-serif;
    font-size: 8.5px;
    letter-spacing: 1px;
    color: var(--red);
    margin-top: 1px;
  }
  .contact__address {
    margin-top: 12px;
    font-size: 11px;
    line-height: 13.5px;
    color: var(--text);
  }
  .contact__lines { margin-top: 9px; list-style: none; }
  .contact__lines li {
    display: flex; align-items: center; gap: 7px;
    font-size: 11px; line-height: 15px; color: var(--text);
  }
  .contact__lines li.phone { font-size: 12px; }
  .contact__lines svg { width: 10px; height: 10px; fill: var(--teal); flex: none; }

  .brand {
    position: absolute;
    right: 50px;
    top: 138px;
    display: flex; align-items: center; gap: 8px;
  }
  .brand__dot { width: 10px; height: 10px; border-radius: 50%; background: var(--teal); }
  .brand__name {
    font-family: "Michroma", Arial, sans-serif;
    font-size: 13px;
    letter-spacing: 1.5px;
    color: var(--teal);
  }
</style>
</head>
<body>
  <section class="card card--front">
    <div class="decor" role="img" aria-label="Faint large brand decoration"></div>
    <div class="contact">
      <h1 class="contact__name">DANA REYES</h1>
      <p class="contact__title">CEO/FOUNDER</p>
      <p class="contact__address">Harborlight Homes<br>214 Willow Street<br>Fairbanks, Alaska 99701</p>
      <ul class="contact__lines">
        <li class="phone">
          <svg viewBox="0 0 24 24"><path d="M6.6 10.8a15.1 15.1 0 0 0 6.6 6.6l2.2-2.2c.3-.3.7-.4 1-.2 1.1.4 2.3.6 3.6.6.6 0 1 .4 1 1V20c0 .6-.4 1-1 1C10.6 21 3 13.4 3 4c0-.6.4-1 1-1h3.5c.6 0 1 .4 1 1 0 1.3.2 2.5.6 3.6.1.3 0 .7-.2 1z"/></svg>
          907 555 0142
        </li>
        <li>
          <svg viewBox="0 0 24 24"><path d="M2 5h20v14H2z M2 5l10 8 10-8" fill="var(--teal)"/><path d="M3 6l9 7 9-7" fill="none" stroke="#f8f8f8" stroke-width="2"/></svg>
          dana@harborlighthomes.org
        </li>
        <li>
          <svg viewBox="0 0 24 24"><circle cx="12" cy="12" r="10"/><path d="M2 12h20M12 2c3 3 3 17 0 20M12 2c-3 3-3 17 0 20" fill="none" stroke="#f8f8f8" stroke-width="1.5"/></svg>
          www.harborlighthomes.org
        </li>
      </ul>
    </div>
  </section>

  <section class="card card--back">
    <div class="decor" role="img" aria-label="Faint large brand decoration"></div>
    <div class="brand">
      <span class="brand__dot"></span>
      <span class="brand__name">HARBORLIGHT HOMES</span>
    </div>
  </section>
</body>
</html>
```